Road Construction Company needs business cards

We would like a new business card designed for our business.

We're a road construction company based in Qld, Australia.

Can the business card please have the following information on it.

Name: Warren Halbeck
Position: General Manager
Phone: 0472 915 348
Email: Warren.halbeck@tovrin.com.au
Address: 87 Marrow Ave, Pendlebay, QLD, 4023
Website: www.tovrin.com.au

Visually we'd like the card to be professional and simple.

Attached is our logo.

Our website is www.tovrin.com.au

Target Market(s)

Men aged 25-60

Contact Information for Business Card

As listed in project description

Font styles to use
Serif

Requirements
Must have
• Large logo on back of card

```html
<!DOCTYPE html>
<html lang="en">
<head>
<meta charset="utf-8">
<title>Tovrin – Business Card</title>
<link href="https://fonts.googleapis.com/css2?family=Questrial&display=swap" rel="stylesheet">
<style>
  :root {
    --bg: #e9e7e3;
    --card: #1f1f21;
    --white: #f2f2f2;
    --blue: #2a8fd6;
    --blue-deep: #1a67c2;
    --muted: #d4d4d4;
    --rule: #2a7fb8;
  }
  * { margin: 0; padding: 0; box-sizing: border-box; }
  html, body {
    width: 1200px; height: 900px; overflow: hidden;
    background: var(--bg);
    font-family: "Questrial", "Century Gothic", sans-serif;
  }
  .canvas {
    width: 1200px; height: 900px;
    display: flex; flex-direction: column;
    align-items: center; justify-content: center; gap: 56px;
  }
  .card {
    position: relative;
    width: 640px; height: 366px;
    background: var(--card);
    border-radius: 34px;
    box-shadow: 0 14px 30px rgba(0,0,0,.25);
    overflow: hidden;
  }
  /* front */
  .card-front { display: flex; align-items: center; justify-content: center; }
  .brand-name {
    font-size: 84px; letter-spacing: 6px; text-transform: uppercase;
    color: var(--white); line-height: 1;
  }
  /* back */
  .holder { position: absolute; left: 40px; top: 44px; }
  .holder-name {
    color: var(--blue); font-size: 22px; text-transform: uppercase; letter-spacing: .5px;
  }
  .holder-role { color: var(--muted); font-size: 17px; margin-top: 6px; margin-left: 12px; }
  .contacts {
    position: absolute; left: 330px; top: 70px;
    list-style: none; color: var(--white); font-size: 15px;
  }
  .contacts li { display: flex; align-items: center; gap: 8px; margin-bottom: 9px; }
  .contacts svg { width: 14px; height: 14px; flex: none; }
  .contacts .accent { color: var(--blue); }
  .divider {
    position: absolute; left: 370px; right: 30px; top: 212px;
    border-top: 1px solid var(--rule);
  }
  .brand-mark {
    position: absolute; right: 40px; bottom: 54px;
    font-size: 66px; letter-spacing: 5px; text-transform: uppercase;
    color: var(--blue-deep); line-height: 1;
  }
</style>
</head>
<body>
<main class="canvas">
  <section class="card card-front" aria-label="Card front">
    <div class="brand-name">Tovrin</div>
  </section>

  <section class="card card-back" aria-label="Card back">
    <div class="holder">
      <p class="holder-name">Warren Halbeck</p>
      <p class="holder-role">General Manager</p>
    </div>

    <ul class="contacts">
      <li>
        <svg viewBox="0 0 24 24" aria-hidden="true"><path fill="#2a8fd6" d="M6.6 10.8a15.1 15.1 0 0 0 6.6 6.6l2.2-2.2a1 1 0 0 1 1-.25 11.4 11.4 0 0 0 3.6.57 1 1 0 0 1 1 1V20a1 1 0 0 1-1 1A17 17 0 0 1 3 4a1 1 0 0 1 1-1h3.5a1 1 0 0 1 1 1c0 1.25.2 2.45.57 3.57a1 1 0 0 1-.25 1z"/></svg>
        <span>0472 915 348</span>
      </li>
      <li>
        <svg viewBox="0 0 24 24" aria-hidden="true"><circle cx="12" cy="12" r="9" fill="none" stroke="#2a8fd6" stroke-width="2.4"/><path d="M3 12h18M12 3c3 3 3 15 0 18M12 3c-3 3-3 15 0 18" fill="none" stroke="#2a8fd6" stroke-width="1.6"/></svg>
        <span>www.<span class="accent">tovrin</span>.com.au</span>
      </li>
      <li>
        <svg viewBox="0 0 24 24" aria-hidden="true"><rect x="2" y="5" width="20" height="14" rx="2" fill="#2a8fd6"/><path d="M3 6l9 7 9-7" fill="none" stroke="#1f1f21" stroke-width="1.8"/></svg>
        <span>Warren.halbeck@<span class="accent">tovrin</span>.com.au</span>
      </li>
      <li>
        <svg viewBox="0 0 24 24" aria-hidden="true"><path fill="#2a8fd6" d="M12 2a7 7 0 0 0-7 7c0 5.2 7 13 7 13s7-7.8 7-13a7 7 0 0 0-7-7zm0 9.5A2.5 2.5 0 1 1 12 6.5a2.5 2.5 0 0 1 0 5z"/></svg>
        <span>87 Marrow Ave, Pendlebay, QLD, 4023</span>
      </li>
    </ul>

    <div class="divider"></div>
    <div class="brand-mark">Tovrin</div>
  </section>
</main>
</body>
</html>
```